SaaS Early tech startup business card design

Unique design for experience ecommerce platform company. the business cards will be used by executive members. conformance with color code is required.

```html
<!DOCTYPE html>
<html lang="en">
<head>
<meta charset="utf-8">
<title>Novix — Business Card</title>
<link rel="stylesheet" href="https://fonts.googleapis.com/css2?family=Source+Sans+3:wght@400;600;700&display=swap">
<style>
  :root {
    --backdrop: #1c1c1d;
    --card: #0c0c0c;
    --card-edge: #1a1a1a;
    --teal: #1cb8a0;
    --ocean: #0f6f9c;
    --ink: #e6e6e6;
    --muted: #cfcfcf;
    --divider: #2c2c2c;
  }
  * { box-sizing: border-box; margin: 0; padding: 0; }
  html, body { width: 1200px; height: 900px; overflow: hidden; }
  body {
    background: radial-gradient(ellipse at 50% 45%, #2a2a2b 0%, var(--backdrop) 70%);
    font-family: "Source Sans 3", Arial, sans-serif;
    display: flex;
    align-items: center;
    justify-content: center;
    gap: 40px;
  }
  .card {
    width: 540px;
    height: 310px;
    background: var(--card);
    border: 1px solid var(--card-edge);
    border-radius: 22px;
    position: relative;
    box-shadow: 0 18px 40px rgba(0,0,0,0.55);
  }
  .card--front { display: flex; }
  .brand-panel {
    width: 47%;
    display: flex;
    align-items: center;
    justify-content: center;
    border-right: 1px solid var(--divider);
    margin: 40px 0;
  }
  .wordmark {
    font-weight: 700;
    font-size: 78px;
    letter-spacing: -1px;
    line-height: 1;
    color: var(--teal);
  }
  .contact-panel {
    flex: 1;
    padding: 62px 0 0 32px;
    color: var(--ink);
  }
  .holder-name {
    font-weight: 600;
    font-size: 21px;
    letter-spacing: 0.5px;
    color: var(--teal);
    line-height: 1.1;
  }
  .holder-role {
    font-size: 15px;
    color: var(--ink);
    margin-bottom: 14px;
  }
  .contact-list { list-style: none; }
  .contact-list li {
    display: flex;
    align-items: center;
    gap: 8px;
    font-size: 15px;
    line-height: 1.45;
  }
  .contact-list svg { width: 13px; height: 13px; flex: none; }
  .accent { color: var(--teal); }
  .address {
    font-size: 15px;
    line-height: 1.3;
    color: var(--muted);
    margin-top: 14px;
    padding-left: 21px;
  }
  .card--back {
    display: flex;
    align-items: center;
    justify-content: center;
  }
  .card--back .wordmark {
    font-size: 110px;
    color: #f2f2f2;
  }
</style>
</head>
<body>
  <section class="card card--front" aria-label="Business card front">
    <div class="brand-panel">
      <span class="wordmark">novix</span>
    </div>
    <div class="contact-panel">
      <p class="holder-name">DANIEL MARSH</p>
      <p class="holder-role">Managing Director</p>
      <ul class="contact-list">
        <li>
          <svg viewBox="0 0 16 16" aria-hidden="true"><path fill="var(--teal)" d="M3.6 1.5l2.3 2.6-1.2 1.9c.9 2 2.6 3.7 4.6 4.6l1.9-1.2 2.6 2.3-1.3 2.3C7 14.2 1.8 9 1.3 3.2z"/></svg>
          <span>021-555 018 342</span>
        </li>
        <li>
          <svg viewBox="0 0 16 16" aria-hidden="true"><rect x="1" y="3" width="14" height="10" fill="var(--teal)"/><path d="M1 3l7 6 7-6" fill="none" stroke="var(--card)" stroke-width="1.4"/></svg>
          <span>hello@novixapp.com</span>
        </li>
        <li>
          <svg viewBox="0 0 16 16" aria-hidden="true"><g fill="none" stroke="var(--teal)" stroke-width="1.3"><circle cx="8" cy="8" r="6.5"/><ellipse cx="8" cy="8" rx="2.8" ry="6.5"/><path d="M1.5 8h13M2.5 4.8h11M2.5 11.2h11"/></g></svg>
          <span>www.<span class="accent">novixapp</span>.com</span>
        </li>
      </ul>
      <p class="address">88 Harbor Lane, Suite 4<br>10231, Eastland</p>
    </div>
  </section>

  <section class="card card--back" aria-label="Business card back">
    <span class="wordmark">novix</span>
  </section>
</body>
</html>
```